Executive Business Card for Healthcare Company [Need Today]

I need a business card design for a healthcare company. The only branding the company has thus far is a logo. The cards will be utilized by company executives. The design I envision will be vibrant and appealing but with a corporate feel. They shouldn't be too casual or playful. I would like to complete this project TODAY if possible.

Target Market(s)

Healthcare vendors, other executives in healthcare and pharmaceuticals

Industry/Entity Type

Pharmaceutical

Contact Information for Business Card

See attachment

Font styles to use
Serif
Sans Serif

Colors

Designer to choose colors to be used in the design.

```html
<!DOCTYPE html>
<html lang="en">
<head>
<meta charset="utf-8">
<title>Corvan Therapeutics – Business Card</title>
<link href="https://fonts.googleapis.com/css2?family=Crimson+Pro:wght@400&family=Source+Sans+3:wght@400&display=swap" rel="stylesheet">
<style>
  :root {
    --ink: #111111;
    --muted: #333333;
    --paper: #ffffff;
    --green-soft: #e9fde9;
    --green-deep: #6ef47a;
    --social: #3a9fd8;
  }
  html, body { margin: 0; padding: 0; overflow: hidden; background: var(--paper); }
  .card {
    position: relative;
    width: 798px;
    height: 1200px;
    overflow: hidden;
    background: linear-gradient(to bottom, var(--paper) 0, var(--paper) 330px, var(--green-soft) 400px, var(--green-deep) 1200px);
    font-family: "Crimson Pro", "Times New Roman", serif;
    color: var(--ink);
  }
  .brand {
    position: absolute;
    left: 0; right: 0; top: 62px;
    text-align: center;
    margin: 0;
    font-family: "Crimson Pro", "Times New Roman", serif;
    font-weight: 400;
    font-size: 68px;
    line-height: 1;
    color: var(--ink);
  }
  .person { position: absolute; left: 0; right: 0; top: 350px; text-align: center; }
  .person-name { font-size: 98px; font-weight: 400; margin: 0; line-height: 1; }
  .person-title { font-size: 45px; margin: 24px 0 0; line-height: 1; }
  .contact { position: absolute; left: 54px; width: 700px; height: 82px; }
  .contact-icon { position: absolute; left: 0; top: 0; width: 82px; height: 82px; }
  .contact-text {
    position: absolute; white-space: nowrap;
    font-family: "Source Sans 3", Arial, sans-serif;
    top: 50%; transform: translateY(-50%);
    line-height: 1;
  }
  .email { top: 584px; }
  .email .contact-text { left: 112px; font-size: 37px; }
  .office { top: 695px; }
  .office .contact-text { left: 104px; font-size: 34px; }
  .mobile { top: 817px; }
  .mobile .contact-text { left: 112px; font-size: 52px; }
  .address { top: 927px; }
  .address .contact-text {
    left: 87px; top: 2px; transform: none;
    font-family: "Crimson Pro", "Times New Roman", serif;
    font-size: 45px; line-height: 60px;
  }
  .social { position: absolute; left: 0; width: 788px; top: 1083px; text-align: center; }
  .social-label { font-size: 31px; margin: 0 0 12px; line-height: 1.1; }
  .social-links { display: flex; justify-content: center; gap: 12px; }
  .social-links span { width: 36px; height: 36px; border-radius: 4px; background: var(--social); }
  .website {
    position: absolute;
    right: 24px; bottom: 30px;
    margin: 0;
    writing-mode: vertical-rl;
    transform: rotate(180deg);
    font-size: 32px;
    letter-spacing: 1px;
    color: var(--muted);
  }
</style>
</head>
<body>
<main class="card">
  <p class="brand">Corvan Therapeutics</p>

  <section class="person">
    <h1 class="person-name">Daniel Morrow</h1>
    <p class="person-title">Senior Director of Marketing</p>
  </section>

  <div class="contact email">
    <svg class="contact-icon" viewBox="0 0 80 80" aria-hidden="true">
      <circle cx="40" cy="40" r="40" fill="#111"/>
      <rect x="21" y="27" width="38" height="26" fill="none" stroke="#fff" stroke-width="3"/>
      <path d="M21 27 L40 43 L59 27 M21 53 L35 39 M59 53 L45 39" fill="none" stroke="#fff" stroke-width="3"/>
    </svg>
    <span class="contact-text">dmorrow@corvanrx.com</span>
  </div>

  <div class="contact office">
    <svg class="contact-icon" viewBox="0 0 80 80" aria-hidden="true">
      <circle cx="40" cy="40" r="40" fill="#111"/>
      <path d="M18 32 Q40 16 62 32 L58 38 L50 35 L50 30 Q40 26 30 30 L30 35 L22 38 Z" fill="#fff"/>
      <path d="M28 40 L52 40 L58 58 L22 58 Z" fill="#fff"/>
      <circle cx="40" cy="49" r="5" fill="#111"/>
    </svg>
    <span class="contact-text">555-210-4837</span>
  </div>

  <div class="contact mobile">
    <svg class="contact-icon" viewBox="0 0 80 80" aria-hidden="true">
      <circle cx="40" cy="40" r="40" fill="#111"/>
      <path d="M27 20 L34 20 L38 31 L33 35 Q37 44 45 48 L49 43 L60 47 L60 54 Q58 61 50 60 Q25 55 20 30 Q20 22 27 20 Z" fill="#fff"/>
    </svg>
    <span class="contact-text">555-734-1206</span>
  </div>

  <div class="contact address">
    <svg class="contact-icon" viewBox="0 0 80 80" aria-hidden="true">
      <circle cx="40" cy="40" r="40" fill="#111"/>
      <path d="M40 18 Q54 18 54 32 Q54 42 40 62 Q26 42 26 32 Q26 18 40 18 Z" fill="#fff"/>
      <circle cx="40" cy="32" r="5" fill="#111"/>
    </svg>
    <span class="contact-text">318 N Linden<br>Street Marlow GA 30612</span>
  </div>

  <section class="social">
    <p class="social-label">Find Us on:</p>
    <div class="social-links">
      <span role="img" aria-label="Social network link"></span>
      <span role="img" aria-label="Social network link"></span>
      <span role="img" aria-label="Social network link"></span>
      <span role="img" aria-label="Social network link"></span>
    </div>
  </section>

  <p class="website">www.corvanrx.com</p>
</main>
</body>
</html>
```